Need help in designing new business card utilizing our new logo.

BuildMark Solutions works with Construction Business Owners, Managers & IT Professionals to strengthen software usage and increase user productivity.

Our Construction Accounting and Mobile Field Management Software Clients engage with us in the following areas:

New Software Implementations
Software Re-Implementations
Redesigning Software Usage at the User Level
Project Coordination & Management
Continued Software Support

Old tag line:
Weighing Options - Implementing Solutions

www.buildmark-solutions.example

Ridge 4 is a product, but not needed for a new business card.

```html
<!DOCTYPE html>
<html lang="en">
<head>
<meta charset="utf-8">
<title>BuildMark Solutions – Business Card</title>
<link href="https://fonts.googleapis.com/css2?family=Montserrat:wght@400;500;600&display=swap" rel="stylesheet">
<style>
  :root {
    --bg: #151515;
    --card: #232323;
    --card-edge: #2c2c2c;
    --brand-blue: #3b3fc8;
    --text-light: #f2f2f2;
    --text-soft: #d8d8d8;
  }
  * { box-sizing: border-box; margin: 0; padding: 0; }
  html, body {
    width: 1200px; height: 900px; overflow: hidden;
    background: var(--bg);
    font-family: "Montserrat", sans-serif;
  }
  .stage { position: relative; width: 1200px; height: 900px; }
  .card {
    position: absolute; left: 280px; width: 640px; height: 366px;
    background: linear-gradient(135deg, var(--card) 0%, var(--card-edge) 100%);
    border-radius: 4px;
    box-shadow: 0 14px 30px rgba(0,0,0,0.55);
  }
  .card--front { top: 70px; }
  .card--back { top: 464px; }

  .brand { display: flex; align-items: center; gap: 12px; }
  .brand__square { width: 30px; height: 30px; background: var(--brand-blue); flex: none; }
  .brand__name {
    font-weight: 600; color: var(--brand-blue); letter-spacing: 0.02em; line-height: 1.1;
  }

  .card--front .brand { position: absolute; top: 108px; left: 0; right: 0; justify-content: center; }
  .card--front .brand__name { font-size: 34px; }
  .services {
    position: absolute; top: 196px; left: 0; right: 0;
    list-style: none; text-align: center;
    color: var(--text-light); font-size: 15px; line-height: 1.45; font-weight: 400;
  }

  .card--back .brand { position: absolute; top: 118px; left: 40px; }
  .card--back .brand__square { width: 22px; height: 22px; }
  .card--back .brand__name { font-size: 21px; }
  .tagline {
    position: absolute; top: 166px; left: 40px;
    color: var(--brand-blue); font-size: 15px; font-weight: 500; line-height: 1.3;
  }
  .divider {
    position: absolute; left: 318px; top: 86px; width: 2px; height: 200px;
    background: var(--brand-blue);
  }
  .person { position: absolute; left: 344px; top: 92px; }
  .person__name { color: var(--brand-blue); font-size: 24px; font-weight: 600; letter-spacing: 0.02em; }
  .person__role { color: var(--text-light); font-size: 15px; margin-top: 2px; }
  .contact { list-style: none; margin-top: 16px; }
  .contact__item {
    display: flex; align-items: center; gap: 10px;
    color: var(--text-light); font-size: 14px; line-height: 1.55;
  }
  .contact__icon { width: 12px; height: 12px; flex: none; }
  .address { color: var(--text-light); font-size: 15px; line-height: 1.45; margin-top: 12px; }
</style>
</head>
<body>
<main class="stage">

  <section class="card card--front">
    <div class="brand">
      <span class="brand__square"></span>
      <span class="brand__name">BuildMark Solutions</span>
    </div>
    <ul class="services">
      <li>New Software Implementations | Software Re-Implementations</li>
      <li>Redesigning Software Usage at the User Level</li>
      <li>Project Coordination &amp; Management</li>
      <li>Continued Software Support</li>
    </ul>
  </section>

  <section class="card card--back">
    <div class="brand">
      <span class="brand__square"></span>
      <span class="brand__name">BuildMark Solutions</span>
    </div>
    <p class="tagline">Construction Accounting<br>Software Consultants</p>

    <div class="divider"></div>

    <div class="person">
      <h1 class="person__name">Dana R. Whitfield</h1>
      <p class="person__role">Owner</p>
      <ul class="contact">
        <li class="contact__item">
          <svg class="contact__icon" viewBox="0 0 12 12"><path d="M2 1h2.5l1 3-1.5 1c.6 1.3 1.7 2.4 3 3l1-1.5 3 1V10a1 1 0 0 1-1 1C5 11 1 7 1 2a1 1 0 0 1 1-1z" fill="var(--brand-blue)"/></svg>
          866-555-0142 ext.100
        </li>
        <li class="contact__item">
          <svg class="contact__icon" viewBox="0 0 12 12"><rect x="3" y="0.5" width="6" height="11" rx="1" fill="none" stroke="var(--brand-blue)" stroke-width="1.2"/><circle cx="6" cy="9.5" r="0.7" fill="var(--brand-blue)"/></svg>
          518-555-0188
        </li>
        <li class="contact__item">
          <svg class="contact__icon" viewBox="0 0 12 12"><rect x="0.6" y="2.5" width="10.8" height="7" fill="none" stroke="var(--brand-blue)" stroke-width="1.1"/><path d="M0.6 2.5 6 6.5l5.4-4" fill="none" stroke="var(--brand-blue)" stroke-width="1.1"/></svg>
          dana.whitfield@buildmark-solutions.example
        </li>
        <li class="contact__item">
          <svg class="contact__icon" viewBox="0 0 12 12"><circle cx="6" cy="6" r="5.2" fill="none" stroke="var(--brand-blue)" stroke-width="1.1"/><ellipse cx="6" cy="6" rx="2.2" ry="5.2" fill="none" stroke="var(--brand-blue)" stroke-width="1"/><path d="M0.8 6h10.4" stroke="var(--brand-blue)" stroke-width="1"/></svg>
          www.buildmark-solutions.example
        </li>
      </ul>
      <p class="address">14B Market Street - PMB 118<br>Hudson Falls NY 12839</p>
    </div>
  </section>

</main>
</body>
</html>
```